Business Cards for a law firm

Business cards for our law firm. Use our silhoette logo and OAK PARTNERS - check our website (www.oakpartners.example)

Contact Information for Business Card

our silhouette logo, OAK PARTNERS, 800-555-0147, Dorian Pemberton, dorian@oakpartners.example

Requirements
Must have
• our silhouette logo, OAK PARTNERS, 800-555-0147, Dorian Pemberton, dorian@oakpartners.example

```html
<!DOCTYPE html>
<html lang="en">
<head>
<meta charset="utf-8">
<title>Oak Partners – Business Cards</title>
<link href="https://fonts.googleapis.com/css2?family=Montserrat:wght@400;500;600&family=Source+Sans+3:wght@700&display=swap" rel="stylesheet">
<style>
  :root {
    --navy: #23336a;
    --ink: #1d1d1f;
    --paper: #ffffff;
    --backdrop: #e9e9eb;
  }
  * { margin: 0; padding: 0; box-sizing: border-box; }
  html, body {
    width: 1200px; height: 1108px; overflow: hidden;
    background: var(--backdrop);
    font-family: "Montserrat", sans-serif;
  }
  .card { position: absolute; width: 776px; }
  .card-front { left: 219px; top: 50px; height: 473px; background: var(--paper); }
  .card-back { left: 217px; top: 568px; height: 456px; background: var(--navy); }

  .brand { position: absolute; display: flex; align-items: center; }
  .brand-mark { display: block; }
  .brand-name {
    font-family: "Montserrat", sans-serif; font-weight: 600;
    text-transform: uppercase; white-space: nowrap;
  }
  .card-front .brand { left: 100px; top: 240px; gap: 12px; }
  .card-front .brand-mark { width: 40px; height: 40px; background: var(--navy); }
  .card-front .brand-name { color: var(--navy); font-size: 19px; letter-spacing: 2px; }

  .divider {
    position: absolute; left: 389px; top: 185px;
    width: 2px; height: 158px; background: var(--navy);
  }
  .contact { position: absolute; left: 403px; top: 182px; }
  .person-name {
    font-family: "Source Sans 3", sans-serif; font-weight: 700;
    font-size: 32px; color: var(--navy); line-height: 1.1;
  }
  .person-role { font-size: 17px; color: var(--ink); margin-top: 2px; margin-bottom: 12px; }
  .contact-list { list-style: none; }
  .contact-list li {
    display: flex; align-items: center; gap: 9px;
    font-size: 17px; color: var(--ink); height: 31px;
  }
  .contact-list svg { width: 17px; height: 17px; fill: var(--navy); flex: none; }

  .card-back .brand { left: 84px; top: 196px; gap: 24px; }
  .card-back .brand-mark { width: 84px; height: 84px; background: var(--paper); }
  .card-back .brand-name { color: var(--paper); font-size: 46px; letter-spacing: 4px; }
</style>
</head>
<body>
  <section class="card card-front">
    <div class="brand">
      <span class="brand-mark"></span>
      <span class="brand-name">Oak Partners</span>
    </div>
    <div class="divider"></div>
    <div class="contact">
      <p class="person-name">Dorian Pemberton</p>
      <p class="person-role">Lawyer</p>
      <ul class="contact-list">
        <li>
          <svg viewBox="0 0 24 24" aria-hidden="true"><path d="M6.6 10.8a15.1 15.1 0 0 0 6.6 6.6l2.2-2.2c.3-.3.7-.4 1-.2 1.1.4 2.3.6 3.6.6.6 0 1 .4 1 1V20c0 .6-.4 1-1 1A17 17 0 0 1 3 4c0-.6.4-1 1-1h3.5c.6 0 1 .4 1 1 0 1.3.2 2.5.6 3.6.1.3 0 .7-.2 1z"/></svg>
          800-555-0147
        </li>
        <li>
          <svg viewBox="0 0 24 24" aria-hidden="true"><path d="M3 6h18v12H3z" opacity="0"/><path d="M3 6.5 12 12l9-5.5V6H3zM3 8.6V18h18V8.6L12 14z"/></svg>
          dorian@oakpartners.example
        </li>
        <li>
          <svg viewBox="0 0 24 24" aria-hidden="true"><path d="M12 2a10 10 0 1 0 0 20 10 10 0 0 0 0-20zm-1 17.9A8 8 0 0 1 4.1 10L9 15v1a2 2 0 0 0 2 2zm6.9-2.5A2 2 0 0 0 16 16h-1v-3a1 1 0 0 0-1-1H8v-2h2a1 1 0 0 0 1-1V7h2a2 2 0 0 0 2-2v-.4a8 8 0 0 1 2.9 12.8z"/></svg>
          www.oakpartners.example
        </li>
      </ul>
    </div>
  </section>

  <section class="card card-back">
    <div class="brand">
      <span class="brand-mark"></span>
      <span class="brand-name">Oak Partners</span>
    </div>
  </section>
</body>
</html>
```